Business Card for Fashion House

We need a business card design for our personalize fashion service for our customers. the business card should reflect reliability, luxury and creativity.
The brand Gravetto is extracted from "Graceful Velvetto"; Gravetto provides fashion designs sprinkled with luxury and style tailored for our elite clients character profile.
Gravetto is created for those who embody class and elegance with a passion for style.
Target Market(s)
Affluent Customers
Industry/Entity Type
Fashion
Contact Information for Business Card
Samira Haddadin
Fashion Designer
Telephone: +971 4 555 0192
Mobile +971 50 555 0147
Emal info@gravetto-example.com
Website www.gravetto-example.com
Social Media Youtube g+ Facebook Instagram Pin /gravetto
Font styles to use
Other font styles liked:
- Audrey provided
Look and feel
Each slider illustrates characteristics of the customer's brand and the style your logo design should communicate.

```html
<!DOCTYPE html>
<html lang="en">
<head>
<meta charset="utf-8">
<title>Gravetto Business Card</title>
<link rel="stylesheet" href="https://fonts.googleapis.com/css2?family=Marcellus&family=Cinzel:wght@400&display=swap">
<style>
  :root {
    --backdrop: #2b2b2b;
    --ink: #0b0b0b;
    --paper: #ffffff;
    --paper-soft: #e9e9e9;
    --rule: #8a8a8a;
  }
  * { margin: 0; padding: 0; box-sizing: border-box; }
  html, body { width: 1200px; height: 880px; overflow: hidden; }
  body {
    background: var(--backdrop);
    font-family: "Marcellus", Georgia, serif;
    display: flex; flex-direction: column; align-items: center; justify-content: center;
    gap: 44px;
  }
  .card {
    position: relative;
    width: 640px; height: 366px;
    border-radius: 22px;
    overflow: hidden;
  }
  /* Back side */
  .card-back { background: var(--ink); color: var(--paper); }
  .brand {
    position: absolute; left: 0; right: 0;
    display: flex; flex-direction: column; align-items: center;
  }
  .brand-mark {
    width: 58px; height: 58px; border-radius: 50%;
    border: 3px solid currentColor;
    margin-bottom: 22px;
  }
  .brand-name {
    font-family: "Cinzel", Georgia, serif;
    font-size: 24px; letter-spacing: 0.62em; text-indent: 0.62em;
    text-transform: uppercase;
  }
  .card-back .brand { top: 78px; }
  .social-row {
    position: absolute; left: 0; right: 0; top: 262px;
    display: flex; justify-content: center; gap: 12px;
  }
  .social-dot {
    width: 30px; height: 30px; border-radius: 50%;
    border: 2px solid var(--paper);
  }
  /* Front side */
  .card-front { background: var(--paper); color: var(--ink); }
  .card-front .brand { top: 44px; }
  .contact-band {
    position: absolute; left: 0; right: 0; top: 210px; height: 118px;
    background: var(--ink); color: var(--paper);
    display: flex; align-items: center;
    padding: 0 34px;
    border-top: 3px solid var(--paper-soft);
    box-shadow: inset 0 5px 0 var(--ink), inset 0 6px 0 var(--rule);
  }
  .person { width: 190px; align-self: flex-end; padding-bottom: 20px; }
  .person-name { font-size: 20px; letter-spacing: 0.02em; }
  .person-role { font-size: 14px; color: var(--paper-soft); margin-top: 2px; }
  .divider { width: 1px; height: 48px; background: var(--rule); margin: 0 22px; }
  .contact-list { list-style: none; display: flex; flex-direction: column; gap: 8px; font-size: 14px; }
  .contact-list li { display: flex; align-items: center; gap: 8px; white-space: nowrap; }
  .contact-icon {
    width: 20px; height: 20px; flex: none;
    border-radius: 50%; border: 1.5px solid var(--paper);
    display: flex; align-items: center; justify-content: center;
  }
  .contact-icon svg { width: 12px; height: 12px; stroke: var(--paper); fill: none; stroke-width: 1.6; stroke-linecap: round; stroke-linejoin: round; }
  .card-front .bottom-rule {
    position: absolute; left: 0; right: 0; top: 338px; height: 1px; background: var(--rule);
  }
</style>
</head>
<body>

<section class="card card-back" aria-label="Card back">
  <div class="brand">
    <div class="brand-mark"></div>
    <div class="brand-name">Gravetto</div>
  </div>
  <div class="social-row" aria-label="Social channels /gravetto">
    <span class="social-dot"></span>
    <span class="social-dot"></span>
    <span class="social-dot"></span>
    <span class="social-dot"></span>
    <span class="social-dot"></span>
  </div>
</section>

<section class="card card-front" aria-label="Card front">
  <div class="brand">
    <div class="brand-mark"></div>
    <div class="brand-name">Gravetto</div>
  </div>

  <div class="contact-band">
    <div class="person">
      <div class="person-name">Samira Haddadin</div>
      <div class="person-role">Fashion Designer</div>
    </div>
    <span class="divider"></span>
    <ul class="contact-list">
      <li>
        <span class="contact-icon"><svg viewBox="0 0 12 12"><path d="M3 1.5 L4.5 4 L3.5 5 Q4.5 7.5 7 8.5 L8 7.5 L10.5 9 L9.5 10.5 Q4 10.5 1.5 3 Z"/></svg></span>
        +971 4 555 0192
      </li>
      <li>
        <span class="contact-icon"><svg viewBox="0 0 12 12"><rect x="3.5" y="1" width="5" height="10" rx="1"/><path d="M5.5 9.2 H6.5"/></svg></span>
        +971 50 555 0147
      </li>
    </ul>
    <span class="divider"></span>
    <ul class="contact-list">
      <li>
        <span class="contact-icon"><svg viewBox="0 0 12 12"><rect x="1.5" y="3" width="9" height="6"/><path d="M1.5 3 L6 6.5 L10.5 3"/></svg></span>
        info@gravetto-example.com
      </li>
      <li>
        <span class="contact-icon"><svg viewBox="0 0 12 12"><circle cx="6" cy="6" r="4.5"/><path d="M1.5 6 H10.5 M6 1.5 Q3.5 6 6 10.5 M6 1.5 Q8.5 6 6 10.5"/></svg></span>
        www.gravetto-example.com
      </li>
    </ul>
  </div>
  <div class="bottom-rule"></div>
</section>

</body>
</html>
```